Book cover for book about Climate Change

Looking for a clean, bold, and attractive cover for a mass-market paperback (5.5"x 8.5") about solving the climate change problem. Title is either "Where the Rivers Meet” or A Harbor Made of Glass” (your choice), subtitle is "A practical field guide to mending the weather — so that the young ones after us inherit steady seasons and open skies," author is Lorne Whitcombe. Thinking that it *might* feature an image of Earth (or a portion thereof) and its very thin layer of atmosphere -- but STRONGLY encourage other ideas too!

Requirements
Nice to have
• Keep it positive — NOT scary doom-and-gloom

```html
<!DOCTYPE html>
<html lang="en">
<head>
<meta charset="utf-8">
<title>Where the Rivers Meet — Lorne Whitcombe</title>
<link rel="stylesheet" href="https://fonts.googleapis.com/css2?family=Anton&family=Arimo:wght@700&display=swap">
<style>
  :root {
    --page: #ffffff;
    --plum-core: #6b1a66;
    --plum-mid: #561650;
    --plum-edge: #3c0f37;
    --author: #bc9fc0;
    --title: #ffffff;
    --accent: #fcc50a;
    --subtitle: #ffffff;
  }
  * { margin: 0; padding: 0; box-sizing: border-box; }
  html, body {
    width: 1200px;
    height: 1200px;
    overflow: hidden;
    background: var(--page);
  }
  .cover {
    position: absolute;
    left: 240px;
    top: 48px;
    width: 720px;
    height: 1110px;
    background: radial-gradient(ellipse 70% 60% at 50% 50%, var(--plum-core) 0%, var(--plum-mid) 55%, var(--plum-edge) 100%);
    text-align: center;
  }
  .author {
    position: absolute;
    top: 58px;
    left: 0;
    right: 0;
    font-family: "Arimo", Arial, sans-serif;
    font-weight: 700;
    font-size: 60px;
    line-height: 1;
    letter-spacing: 0.5px;
    white-space: nowrap;
    color: var(--author);
    text-transform: uppercase;
  }
  .title {
    position: absolute;
    top: 150px;
    left: 0;
    right: 0;
    height: 760px;
    display: flex;
    flex-direction: column;
    justify-content: center;
    align-items: center;
    font-family: "Anton", Impact, sans-serif;
    font-weight: 400;
    text-transform: uppercase;
  }
  .title-line {
    display: block;
    font-size: 172px;
    line-height: 158px;
    letter-spacing: 0;
    white-space: nowrap;
    color: var(--title);
  }
  .title-line--accent { color: var(--accent); }
  .subtitle {
    position: absolute;
    top: 930px;
    left: 40px;
    right: 40px;
    font-family: "Arimo", Arial, sans-serif;
    font-weight: 700;
    font-size: 22.5px;
    line-height: 32.5px;
    color: var(--subtitle);
    text-transform: uppercase;
  }
  .subtitle .highlight { color: var(--accent); }
</style>
</head>
<body>
  <main class="cover">
    <p class="author">Lorne Whitcombe</p>
    <h1 class="title" aria-label="Where the Rivers Meet">
      <span class="title-line">Where</span>
      <span class="title-line">The</span>
      <span class="title-line">Rivers</span>
      <span class="title-line title-line--accent">Meet</span>
    </h1>
    <p class="subtitle">
      A practical <span class="highlight">field guide</span> to <span class="highlight">mending</span><br>
      the weather — so that the young<br>
      ones after us inherit steady<br>
      seasons and open skies.
    </p>
  </main>
</body>
</html>
```